Allied Health team of Physiotherapists & Occupational Therapists seek a business card design

We have our new logo, we now need our new business cards and stationary. Tidewell: Oedema & Family Clinic is seeking a generic card design to represent our whole team and individual cards for each therapist that incorporates our new logo to communicate our holistic approach that is calming, nuturing, supportive and welcoming.
Our Physiotherapists and Occupational Therapists assess, treat and provide education for people who are at risk of or who have lymphoedema. This is often as a result of treatment for cancer. We provide pre-operative and post-operative management and cancer rehabilitation in our Pilates studio. Our team also consists of Physiotherapists who have a strong interest in pelvic floor and continence management for both men and women.

Target Market(s)

Mainly women health conscious

Industry/Entity Type

Allied Health: Physiotherapy / Occupational Therapy

Contact Information for Business Card

Address: 14 Gallivant Ave Frankston 3199 Phone: 84316570 fax: 8431 6578 Email: info@tidewellcareservices.com.au Website: tidewellcareservices.com.au Facebook address: facebook.com/TidewellOedemaAndFamilyCareClinic. Room to write appointments. Individual cards need to have name, office email and individual email and professional details

Requirements
Must have
• Logo as per uploaded documents

```html
<!DOCTYPE html>
<html lang="en">
<head>
<meta charset="utf-8">
<title>Tidewell: Oedema &amp; Family Clinic – Business Card</title>
<link rel="stylesheet" href="https://fonts.googleapis.com/css2?family=Arimo:wght@400&family=Open+Sans:wght@400&display=swap">
<style>
  :root {
    --peach: #f8b084;
    --sage: #c4cec4;
    --paper: #ffffff;
    --ink: #1e1e1e;
    --backdrop: #4a4b4d;
  }
  * { margin: 0; padding: 0; box-sizing: border-box; }
  html, body { width: 1200px; height: 964px; overflow: hidden; }
  body {
    background: var(--backdrop);
    font-family: "Arimo", Arial, sans-serif;
    color: var(--ink);
    position: relative;
  }
  .card {
    position: absolute;
    left: 250px;
    width: 700px;
    height: 400px;
    overflow: hidden;
    box-shadow: 0 6px 18px rgba(0,0,0,.35);
  }
  .card--front { top: 50px; background: var(--peach); }
  .card--back { top: 514px; background: var(--paper); }

  /* brand name block */
  .brand {
    display: flex;
    align-items: center;
    gap: 14px;
  }
  .brand__dot {
    width: 18px; height: 18px;
    border-radius: 50%;
    flex: none;
  }
  .brand__name {
    font-size: 26px;
    line-height: 1.2;
    font-weight: 400;
  }
  .card--front .brand {
    position: absolute;
    left: 50%; top: 50%;
    transform: translate(-50%, -50%);
    width: 300px;
  }
  .card--front .brand__dot { border: 2px solid var(--paper); }
  .card--front .brand__name { color: var(--paper); }

  .card--back .brand {
    position: absolute;
    left: 40px; top: 38px;
    width: 220px;
  }
  .card--back .brand__dot { border: 2px solid var(--peach); width: 14px; height: 14px; }
  .card--back .brand__name { color: var(--peach); font-size: 18px; }

  .swoosh { position: absolute; inset: 0; width: 700px; height: 400px; }

  .person {
    position: absolute;
    left: 420px; top: 150px;
  }
  .person__name { font-size: 22px; letter-spacing: .3px; }
  .person__role { font-family: "Open Sans", Arial, sans-serif; font-size: 10px; margin-top: 2px; }

  .address {
    position: absolute;
    left: 40px; top: 170px;
    font-size: 17px;
    line-height: 1.3;
  }
  .contacts {
    position: absolute;
    left: 40px; top: 232px;
    list-style: none;
    font-size: 16px;
  }
  .contacts li {
    display: flex;
    align-items: center;
    gap: 14px;
    height: 30px;
  }
  .contacts svg { width: 18px; height: 18px; flex: none; }
</style>
</head>
<body>

<section class="card card--front" aria-label="Card front">
  <div class="brand">
    <span class="brand__dot"></span>
    <span class="brand__name">Tidewell: Oedema &amp; Family Clinic</span>
  </div>
</section>

<section class="card card--back" aria-label="Card back">
  <svg class="swoosh" viewBox="0 0 700 400" aria-hidden="true">
    <path d="M360,0 H700 V400 H470 C610,250 640,110 560,45 C510,8 440,0 360,0 Z" fill="var(--sage)"/>
    <path d="M440,8 C560,10 620,50 630,120 C640,200 560,320 470,400" fill="none" stroke="var(--paper)" stroke-width="8"/>
    <path d="M470,0 H700 V400 H470 C580,290 650,160 620,80 C600,30 540,10 470,0 Z" fill="var(--peach)"/>
    <path d="M470,0 C540,10 600,30 620,80 C650,160 580,290 470,400" fill="none" stroke="var(--paper)" stroke-width="6"/>
    <path d="M640,0 H700 V400 H620 C690,300 710,150 640,0 Z" fill="var(--sage)"/>
    <path d="M640,0 C710,150 690,300 620,400" fill="none" stroke="var(--paper)" stroke-width="6"/>
  </svg>

  <div class="brand">
    <span class="brand__dot"></span>
    <span class="brand__name">Tidewell: Oedema &amp; Family Clinic</span>
  </div>

  <div class="person">
    <p class="person__name">JANE HARLOW</p>
    <p class="person__role">CEO/Managing Director</p>
  </div>

  <p class="address">14 Gallivant Ave Frankston,<br>VIC, AU</p>

  <ul class="contacts">
    <li>
      <svg viewBox="0 0 24 24"><path d="M6.6 10.8a15 15 0 0 0 6.6 6.6l2.2-2.2c.3-.3.7-.4 1-.2 1.1.4 2.3.6 3.6.6.6 0 1 .4 1 1V20c0 .6-.4 1-1 1A17 17 0 0 1 3 4c0-.6.4-1 1-1h3.5c.6 0 1 .4 1 1 0 1.3.2 2.5.6 3.6.1.3 0 .7-.2 1z" fill="var(--ink)"/></svg>
      <span>84316570</span>
    </li>
    <li>
      <svg viewBox="0 0 24 24"><rect x="6" y="2" width="12" height="20" rx="2" fill="none" stroke="var(--ink)" stroke-width="2"/><circle cx="12" cy="18" r="1.2" fill="var(--ink)"/></svg>
      <span>8431 6578</span>
    </li>
    <li>
      <svg viewBox="0 0 24 24"><rect x="2" y="5" width="20" height="14" fill="var(--ink)"/><path d="M2 5l10 8 10-8" fill="none" stroke="var(--paper)" stroke-width="1.6"/></svg>
      <span>info@tidewellcareservices.com.au</span>
    </li>
    <li>
      <svg viewBox="0 0 24 24"><circle cx="12" cy="12" r="9" fill="none" stroke="var(--ink)" stroke-width="1.8"/><ellipse cx="12" cy="12" rx="4" ry="9" fill="none" stroke="var(--ink)" stroke-width="1.5"/><path d="M3 12h18M5 7h14M5 17h14" stroke="var(--ink)" stroke-width="1.5"/></svg>
      <span>tidewellcareservices.com.au</span>
    </li>
  </ul>
</section>

</body>
</html>
```